New Business Card Design Project

Need a design that will create an impact / strong impression towards our clients for our business. We are in the lighting business and we do lighting retrofits for large commercial to industrial clientele.

Target Market(s)

Lighting Industry

Industry/Entity Type

Business

Font styles to use
Other font styles liked:
• we would like to use the font on our logo, not sure what it is though..

Requirements
Must have
• Our logo.
Nice to have
• We are open to suggestions that have to do with lighting.

```html
<!DOCTYPE html>
<html lang="en">
<head>
<meta charset="utf-8">
<title>Kinetic Watt Retrofit – Business Card</title>
<link href="https://fonts.googleapis.com/css2?family=Roboto:wght@400;500;700&family=Roboto+Condensed:wght@500;700&display=swap" rel="stylesheet">
<style>
  :root {
    --backdrop: #5a4838;
    --card-front: #f1f2f1;
    --forest: #0f3a10;
    --leaf: #1b8a3c;
    --ink: #454545;
    --paper-white: #ffffff;
  }
  * { margin: 0; padding: 0; box-sizing: border-box; }
  html, body { width: 1200px; height: 960px; overflow: hidden; }
  body {
    background: var(--backdrop);
    font-family: "Roboto", Arial, sans-serif;
    position: relative;
  }
  .card {
    position: absolute;
    width: 600px;
    height: 343px;
    box-shadow: 2px 3px 5px rgba(0,0,0,0.45);
  }
  .card-front { left: 314px; top: 113px; background: var(--card-front); }
  .card-back { left: 312px; top: 472px; background: var(--forest); }

  .name-tab {
    position: absolute; left: 0; top: 47px;
    width: 14px; height: 43px; background: var(--forest);
  }
  .holder-name {
    position: absolute; left: 45px; top: 45px;
    font-family: "Roboto Condensed", Arial, sans-serif;
    font-weight: 700; font-size: 23px; color: var(--forest);
  }
  .holder-title {
    position: absolute; left: 45px; top: 73px;
    font-family: "Roboto Condensed", Arial, sans-serif;
    font-weight: 500; font-size: 15px; color: var(--leaf);
  }
  .address {
    position: absolute; left: 45px; top: 151px;
    font-size: 14.5px; line-height: 19px; color: var(--ink);
  }
  .contacts {
    position: absolute; left: 45px; top: 196px;
    list-style: none; font-size: 14.5px; color: var(--ink);
  }
  .contacts li { display: flex; align-items: center; height: 19px; }
  .contacts svg { width: 14px; height: 14px; margin-right: 9px; fill: var(--forest); }
  .rule {
    position: absolute; left: 45px; top: 287px;
    width: 511px; height: 1px; background: var(--leaf);
  }
  .web-front {
    position: absolute; left: 45px; top: 290px;
    font-size: 14px; letter-spacing: 1.6px; color: var(--ink);
  }
  .brand {
    position: absolute; display: flex; align-items: center; gap: 10px;
    font-family: "Roboto Condensed", Arial, sans-serif; font-weight: 700;
  }
  .brand-front { right: 44px; top: 244px; color: var(--forest); font-size: 22px; }
  .brand-square { width: 20px; height: 20px; background: currentColor; }
  .brand-back {
    left: 0; right: 0; top: 133px; justify-content: center;
    color: var(--paper-white); font-size: 34px;
  }
  .brand-back .brand-square { width: 30px; height: 30px; }
  .web-back {
    position: absolute; left: 0; right: 0; top: 282px; text-align: center;
    font-size: 14px; letter-spacing: 2.4px; color: var(--paper-white);
  }
</style>
</head>
<body>
  <section class="card card-front">
    <div class="name-tab"></div>
    <h1 class="holder-name">DANIEL REYES</h1>
    <p class="holder-title">CEO/FOUNDER</p>
    <p class="address">2140 Alder Court<br>Fairbanks, Alaska 99701</p>
    <ul class="contacts">
      <li><svg viewBox="0 0 24 24"><path d="M6.6 10.8a15 15 0 0 0 6.6 6.6l2.2-2.2c.3-.3.7-.4 1-.2 1.1.4 2.3.6 3.6.6.6 0 1 .4 1 1V20c0 .6-.4 1-1 1A17 17 0 0 1 3 4c0-.6.4-1 1-1h3.5c.6 0 1 .4 1 1 0 1.3.2 2.5.6 3.6.1.3 0 .7-.2 1z"/></svg>555 210 4471</li>
      <li><svg viewBox="0 0 24 24"><path d="M7 1h10a2 2 0 0 1 2 2v18a2 2 0 0 1-2 2H7a2 2 0 0 1-2-2V3a2 2 0 0 1 2-2zm0 3v14h10V4z"/></svg>555 386 9027</li>
      <li><svg viewBox="0 0 24 24"><path d="M6 2h12v6H6zM3 9h18a1 1 0 0 1 1 1v8h-4v4H6v-4H2v-8a1 1 0 0 1 1-1zm5 7v4h8v-4z"/></svg>555 742 1186</li>
      <li><svg viewBox="0 0 24 24"><path d="M2 5h20v14H2zm2 2v.5l8 5 8-5V7z"/></svg>daniel@kwretrofit.com</li>
    </ul>
    <div class="brand brand-front"><span class="brand-square"></span>KINETIC WATT RETROFIT, LLC</div>
    <div class="rule"></div>
    <p class="web-front">www.kwretrofit.com</p>
  </section>

  <section class="card card-back">
    <div class="brand brand-back"><span class="brand-square"></span>KINETIC WATT RETROFIT, LLC</div>
    <p class="web-back">www.kineticwattretrofit.com</p>
  </section>
</body>
</html>
```